Business Card Design needed for start up company Halvora

In need of a new business card designed for a start up company based in Sydney, Halvora is a new start up innovative Company, our mission it to make property accessible for everyday Australian and to become the leading Real Estate platform in Australia. We want it to be fresh and clean.

Industry/Entity Type

Financial

Contact Information for Business Card

Section for Name
Section for Title

HALVORA - The Strength of Pooling
Mobile:
Direct:

Font styles to use
Sans Serif

Colors
33a6d7
0692cd
0255a3
ffffff

Requirements
Must have
• Logo, all business card details

```html
<!DOCTYPE html>
<html lang="en">
<head>
<meta charset="utf-8">
<title>Halvora Business Card</title>
<link rel="stylesheet" href="https://fonts.googleapis.com/css2?family=Jost:wght@400;500;700&display=swap">
<style>
  :root {
    --stage: #2a2a2a;
    --paper: #f3f3f3;
    --sky: #33a6d7;
    --sky-deep: #0692cd;
    --navy: #0255a3;
    --navy-ink: #1f3f7a;
    --white: #ffffff;
    --ink: #3c3c3c;
    --rule: #9a9a9a;
  }
  * { margin: 0; padding: 0; box-sizing: border-box; }
  html, body { width: 1200px; height: 960px; overflow: hidden; }
  body {
    background: var(--stage);
    font-family: "Jost", sans-serif;
    position: relative;
  }
  .card {
    position: absolute;
    width: 600px;
    height: 342px;
    border-radius: 18px;
    overflow: hidden;
  }
  .card-front { left: 302px; top: 124px; background: var(--paper); }
  .card-back { left: 299px; top: 493px; background: var(--sky); }

  .brand {
    position: absolute;
    display: flex;
    align-items: center;
    font-weight: 700;
    letter-spacing: 0.5px;
    line-height: 1;
  }
  .brand-dot { border-radius: 50%; flex: none; }
  .card-front .brand { right: 30px; top: 34px; gap: 10px; font-size: 46px; color: var(--navy-ink); }
  .card-front .brand-dot { width: 78px; height: 78px; background: var(--sky); }
  .card-back .brand { left: 123px; top: 114px; gap: 14px; font-size: 64px; color: var(--white); }
  .card-back .brand-dot { width: 108px; height: 108px; background: var(--white); }

  .holder { position: absolute; left: 28px; top: 187px; }
  .holder-name { font-size: 21px; font-weight: 700; color: var(--navy-ink); line-height: 1.1; }
  .holder-title { font-size: 15px; font-weight: 400; color: var(--sky); line-height: 1.3; }
  .divider { position: absolute; left: 28px; right: 30px; top: 240px; height: 1.5px; background: var(--rule); }

  .contact-list {
    position: absolute; left: 28px; top: 251px;
    list-style: none; font-size: 14px; color: var(--ink); line-height: 19.5px;
  }
  .contact-list li { display: flex; align-items: center; gap: 8px; }
  .contact-list svg { width: 13px; height: 13px; fill: var(--navy-ink); flex: none; }
  .address {
    position: absolute; right: 30px; top: 251px;
    text-align: right; font-style: normal; font-size: 14px; color: var(--ink); line-height: 19.5px;
  }
  .edge-line { position: absolute; left: 0; right: 0; top: 328px; height: 3px; background: var(--sky); }
  .edge-band { position: absolute; left: 0; right: 0; top: 333px; height: 9px; background: var(--navy-ink); }

  .tagline {
    position: absolute; left: 0; right: 0; top: 285px;
    text-align: center; font-size: 16px; color: var(--white);
  }
</style>
</head>
<body>
  <section class="card card-front">
    <div class="brand"><span class="brand-dot"></span><span class="brand-name">HALVORA</span></div>
    <div class="holder">
      <p class="holder-name">MAYA TORREN</p>
      <p class="holder-title">CEO/FOUNDER</p>
    </div>
    <div class="divider"></div>
    <ul class="contact-list">
      <li><svg viewBox="0 0 16 16" aria-hidden="true"><path d="M3.6 1.2l2.3 2.6-1.4 1.8c.9 2 2.6 3.9 4.8 5l1.7-1.4 2.7 2.2-1.3 2.5C6.8 13.4 2.4 8.6 1.6 2.4z"/></svg>612 480 3157</li>
      <li><svg viewBox="0 0 16 16" aria-hidden="true"><path d="M4.5 0h7a1.5 1.5 0 0 1 1.5 1.5v13A1.5 1.5 0 0 1 11.5 16h-7A1.5 1.5 0 0 1 3 14.5v-13A1.5 1.5 0 0 1 4.5 0zm.5 2v10h6V2zm3 11a1 1 0 1 0 0 2 1 1 0 0 0 0-2z"/></svg>614 229 7083</li>
      <li><svg viewBox="0 0 16 16" aria-hidden="true"><path d="M1 4h14v9H1zm1.4 1L8 9l5.6-4z"/></svg>maya@halvora.com</li>
    </ul>
    <address class="address">
      214 Kellmore Street<br>
      Sydney, NSW 2000<br>
      www.halvora.com
    </address>
    <div class="edge-line"></div>
    <div class="edge-band"></div>
  </section>

  <section class="card card-back">
    <div class="brand"><span class="brand-dot"></span><span class="brand-name">HALVORA</span></div>
    <p class="tagline">The Strength of Pooling</p>
  </section>
</body>
</html>
```